Social Media Graphics - Oakline Push REVISED

Create 6-7 individual social media graphics (square size) to encourage folks to join our online course called:

The Harvest Ledger Circle
How to Launch a Multi-Million Business From Scratch
Sign Up Today!

IMPORTANT: Make the largest and most prominent text on the graphic be: How to Launch a Multi-Million Business From Scratch

For the color scheme of the graphics, let's try a blue color palette; make sure the graphics appeal to both men and women

Make sure each graphic contains 1 of the 3 pics attached (crop pic as needed); and make sure one of the graphics is all TEXT only.

Target Market(s)

men and women looking to start a business

Industry/Entity Type

Entrepreneurship

Colors
0054AA
0677BA
7BADD7
CADEEF
E8F1F8

Requirements
Must have
• All the text and use the 3 pics provided; one graphic can be all text; Simple, modern design that's easy to read

```html
<!DOCTYPE html>
<html lang="en">
<head>
<meta charset="utf-8">
<title>The Harvest Ledger Circle – Sign Up</title>
<link rel="stylesheet" href="https://fonts.googleapis.com/css2?family=Saira+Condensed:wght@700;800&display=swap">
<style>
  :root {
    --blue-deep: #0054AA;
    --blue-field: #004CA3;
    --blue-mid: #0677BA;
    --blue-soft: #7BADD7;
    --blue-pale: #CADEEF;
    --blue-mist: #E8F1F8;
    --blue-ghost: #0A60B4;
  }
  * { margin: 0; padding: 0; box-sizing: border-box; }
  html, body { width: 1200px; height: 1200px; overflow: hidden; background: var(--blue-soft); }
  .post {
    position: relative;
    width: 1200px;
    height: 1200px;
    background: var(--blue-soft);
    font-family: "Saira Condensed", "Arial Narrow", sans-serif;
    text-transform: uppercase;
  }
  .field {
    position: absolute;
    left: 37px; top: 37px;
    width: 1126px; height: 1126px;
    background: var(--blue-field);
    overflow: hidden;
  }
  .backdrop-word {
    position: absolute;
    left: 0; right: 0; top: -60px;
    text-align: center;
    font-weight: 800;
    font-size: 330px;
    line-height: 1;
    letter-spacing: 14px;
    color: var(--blue-ghost);
    white-space: nowrap;
  }
  .portrait {
    position: absolute;
    left: 359px; top: 115px;
    width: 482px; height: 482px;
    border-radius: 50%;
    background: radial-gradient(circle at 50% 40%, var(--blue-pale) 0%, var(--blue-soft) 45%, var(--blue-mid) 100%);
    border: 10px solid #5E9BD4;
  }
  .dome {
    position: absolute;
    left: 478px; top: 445px;
    width: 244px; height: 244px;
    border-radius: 50%;
    background: var(--blue-field);
  }
  .course-name {
    position: absolute;
    left: 343px; top: 566px;
    width: 440px; height: 66px;
    background: var(--blue-mid);
    color: var(--blue-mist);
    font-weight: 700;
    font-size: 38px;
    line-height: 66px;
    text-align: center;
    letter-spacing: 1px;
  }
  .side-bar {
    position: absolute;
    top: 772px;
    width: 62px; height: 40px;
    background: var(--blue-soft);
  }
  .side-bar.left { left: 0; }
  .side-bar.right { right: 0; }
  .headline {
    position: absolute;
    left: 0; right: 0; top: 678px;
    text-align: center;
    font-weight: 800;
    font-size: 72px;
    line-height: 90px;
    letter-spacing: 2px;
    color: var(--blue-pale);
  }
  .headline .accent { color: var(--blue-soft); font-size: 76px; }
  .cta {
    position: absolute;
    left: 377px; top: 962px;
    width: 372px; height: 91px;
    background: var(--blue-pale);
    color: var(--blue-deep);
    font-weight: 800;
    font-size: 36px;
    line-height: 91px;
    text-align: center;
    letter-spacing: 1px;
  }
</style>
</head>
<body>
  <main class="post">
    <section class="field">
      <div class="backdrop-word" aria-hidden="true">Harvest</div>
      <div class="portrait" role="img" aria-label="Photo of the two smiling course hosts, a woman in a pink top and a man in a black shirt"></div>
      <div class="dome" aria-hidden="true"></div>
      <div class="course-name">The Harvest Ledger Circle</div>
      <div class="side-bar left" aria-hidden="true"></div>
      <div class="side-bar right" aria-hidden="true"></div>
      <h1 class="headline">
        How to launch a<br>
        <span class="accent">Multi-million business</span><br>
        From scratch
      </h1>
      <div class="cta">Sign up today!</div>
    </section>
  </main>
</body>
</html>
```